Pellowar

We need logo and wesbsite for a software development company based out of Hyderabad, India focused on startups and mid sized companies focused on build a new software products in USA and Europe countires.

Target Market(s)

startup and midsized companies in teh USA and Europe for software product development.

Industry/Entity Type

software development

Coding

Coded - Design and coding required

Number of Pages Required

5+ page

Requirements
Must have
• latest design concepts and very elegant
Nice to have
• each page should have images that reflects the content
Should not have
• too many colors

```html
<!DOCTYPE html>
<html lang="en">
<head>
<meta charset="utf-8">
<title>Pellowar — Custom Software Development</title>
<link href="https://fonts.googleapis.com/css2?family=Montserrat:wght@400;500;600;700&family=Lato:wght@400;700&family=Playfair+Display:wght@800&display=swap" rel="stylesheet">
<style>
:root{
  --red:#c00f14;
  --ink:#111;
  --text:#333;
  --muted:#555;
  --line:#d9d9d9;
  --dark:#1b1b1b;
  --panel:#f4f4f5;
  --white:#fff;
}
*{box-sizing:border-box;margin:0;padding:0}
html,body{width:1200px;height:3599px;overflow:hidden;background:var(--white)}
body{position:relative;font-family:"Lato",sans-serif;color:var(--text)}
.abs{position:absolute}
.btn{position:absolute;background:var(--red);color:var(--white);font-family:"Montserrat",sans-serif;font-weight:700;font-size:12px;letter-spacing:.3px;border-radius:20px;display:flex;align-items:center;justify-content:center;text-transform:uppercase}
.brand{font-family:"Montserrat",sans-serif;font-weight:500;font-size:26px;color:var(--ink);display:flex;align-items:center;gap:10px}
.brand-dot{width:38px;height:38px;border-radius:50%;background:var(--red)}

/* header */
.header{top:0;left:0;width:1200px;height:74px;background:var(--white)}
.header .brand{position:absolute;left:132px;top:17px}
.nav{position:absolute;right:133px;top:25px;display:flex;gap:28px;align-items:center;font-family:"Montserrat",sans-serif;font-size:13px;font-weight:500;color:var(--ink)}
.nav .active{color:var(--red)}
.nav .contact{background:var(--red);color:var(--white);padding:7px 12px;border-radius:8px;display:flex;align-items:center;gap:6px}

/* hero */
.hero{top:74px;left:0;width:1200px;height:563px;background:linear-gradient(110deg,#b9b6b5 0%,#6f6b6c 35%,#2c3545 65%,#1b2a40 100%)}
.hero-title{top:138px;width:1200px;text-align:center;font-family:"Playfair Display",serif;font-weight:800;font-size:46px;color:var(--white)}
.hero-sub{top:204px;width:1200px;text-align:center;font-family:"Lato",sans-serif;font-size:26px;color:var(--white)}
.hero .btn{left:523px;top:264px;width:155px;height:47px;font-size:15px;border:2px solid var(--white);border-radius:24px}
.dots{top:518px;left:562px;display:flex;gap:8px}
.dots span{width:9px;height:9px;border-radius:50%;background:var(--white)}
.dots span.on{background:var(--red)}

/* stats */
.stats{top:637px;left:0;width:1200px;height:120px;border-bottom:1px solid var(--line)}
.stat{position:absolute;top:24px;width:260px;text-align:center}
.stat b{display:block;font-family:"Montserrat",sans-serif;font-weight:400;font-size:30px;color:var(--red)}
.stat small{display:block;margin-top:8px;font-family:"Montserrat",sans-serif;font-size:14px;color:var(--ink)}
.vline{position:absolute;top:25px;width:2px;height:65px;background:var(--line)}

/* about */
.about-photo{left:132px;top:814px;width:465px;height:362px;background:linear-gradient(90deg,#dcdcd8,#9c9690 50%,#c9c4bd);border-radius:4px}
.h2{font-family:"Montserrat",sans-serif;font-weight:700;color:var(--ink)}
.rule{height:2px;width:112px;background:var(--ink)}
.about-h{left:644px;top:808px;font-size:26px;line-height:34px}
.about-rule{left:644px;top:891px}
.about-lead{left:644px;top:916px;width:420px;font-weight:700;font-size:14px;line-height:22px;color:var(--ink)}
.about-body{left:644px;top:976px;width:423px;font-size:13px;line-height:19.3px;text-align:justify}
.about .btn{left:647px;top:1141px;width:112px;height:35px}

/* process */
.process-h{top:1248px;width:1200px;text-align:center;font-size:26px}
.process-tick{left:603px;top:1303px;width:2px;height:27px;background:var(--red)}
.process{top:1329px;left:0;width:1200px;height:500px;background:linear-gradient(120deg,#3d3c3a,#262626 45%,#413d39 70%,#1e1e1e)}
.cell{position:absolute;color:var(--white);font-family:"Montserrat",sans-serif;font-size:16px;line-height:22px}
.cell svg{display:block;margin-bottom:18px}
.col-alt{position:absolute;top:0;height:500px;background:rgba(255,255,255,.06)}
.row-line{position:absolute;left:0;top:264px;width:1200px;height:1px;background:rgba(255,255,255,.12)}

/* why */
.why{top:1829px;left:0;width:1200px;height:533px;background:linear-gradient(90deg,#f2f2f3,#fafafa 60%,#f2f2f3)}
.why-h{left:52px;top:1888px;font-size:26px}
.why-rule{left:52px;top:1938px;width:60px}
.features{left:52px;top:1980px;width:500px;height:233px;display:grid;grid-template-columns:repeat(3,1fr);grid-template-rows:repeat(2,1fr);border:1px solid var(--line);background:#efefef}
.features div{border:1px solid var(--line);display:flex;align-items:center;padding-left:19px;font-family:"Lato",sans-serif;font-size:11px;line-height:18px;color:#333;text-transform:uppercase}
.why .btn{left:52px;top:2254px;width:113px;height:35px}
.why-photo{left:608px;top:1885px;width:547px;height:415px;background:linear-gradient(135deg,#c8b193,#8d735a 45%,#b4a28d)}

/* build */
.tiles{left:133px;top:2413px;width:429px;height:416px;display:grid;grid-template-columns:1fr 1fr;grid-template-rows:1fr 1fr;gap:9px}
.tiles div{background:linear-gradient(135deg,#2a2f38,#0f141c 60%,#1e2633);border-radius:3px}
.build-h{left:609px;top:2454px;font-size:26px}
.build-rule{left:609px;top:2493px;width:70px}
.build-body{left:610px;top:2522px;width:460px;font-size:13px;line-height:19.5px}
.build-body p{margin-bottom:19px}
.build .btn{left:612px;top:2748px;width:112px;height:35px}

/* cta */
.cta{top:2885px;left:0;width:1200px;height:333px;background:linear-gradient(180deg,#ececec,#e2e2e2)}
.cta-h{top:2937px;width:1200px;text-align:center;font-size:24px}
.cta-sub{top:2980px;width:1200px;text-align:center;font-size:16px;color:var(--ink)}
.cta .btn{left:497px;top:3030px;width:206px;height:46px;border-radius:10px;font-size:13px}

/* footer */
.footer{top:3218px;left:0;width:1200px;height:381px;background:var(--dark)}
.footer .brand{position:absolute;left:132px;top:55px;color:var(--white)}
.foot-nav{position:absolute;left:132px;top:120px;font-family:"Montserrat",sans-serif;font-size:11px;color:var(--white);word-spacing:4px}
.follow{position:absolute;left:131px;top:180px;font-family:"Montserrat",sans-serif;font-size:11px;color:var(--white)}
.social{position:absolute;left:131px;top:209px;display:flex;gap:13px}
.social span{width:41px;height:41px;border-radius:50%;border:1px solid var(--white)}
.copy{position:absolute;left:131px;top:297px;font-family:"Lato",sans-serif;font-size:12px;color:var(--white)}

/* form */
.form{left:533px;top:3140px;width:532px;height:420px;background:var(--white);border:4px solid var(--ink);border-radius:6px}
.form-h{position:absolute;top:26px;width:100%;text-align:center;font-family:"Montserrat",sans-serif;font-weight:600;font-size:19px;line-height:28px;color:var(--ink)}
.field{position:absolute;border:1px solid #999;border-radius:4px;font-size:11px;color:#333;padding:12px 16px}
.submit{position:absolute;left:30px;top:335px;width:469px;height:50px;background:var(--red);border-radius:3px;color:var(--white);font-family:"Montserrat",sans-serif;font-weight:700;font-size:16px;display:flex;align-items:center;justify-content:center;gap:12px}
</style>
</head>
<body>

<header class="abs header">
  <div class="brand"><span class="brand-dot"></span>Pellowar</div>
  <nav class="nav">
    <span class="active">HOME</span><span>ABOUT US</span><span>PRODUCT</span><span>TEAM</span><span>CASE STUDY</span>
    <span class="contact"><svg width="13" height="10" viewBox="0 0 13 10"><rect x=".5" y=".5" width="12" height="9" fill="none" stroke="#fff"/><path d="M.5 .5l6 5 6-5" fill="none" stroke="#fff"/></svg>CONTACT</span>
  </nav>
</header>

<section class="abs hero" role="img" aria-label="Developer typing on a laptop with overlaid binary code">
</section>
<h1 class="abs hero-title">We Deliver the Software You Need</h1>
<p class="abs hero-sub">Custom software to reach your vision.</p>
<div class="abs" style="top:74px;left:0;width:1200px;height:563px">
  <div class="btn" style="left:523px;top:264px;width:155px;height:47px;font-size:15px;border:2px solid #fff">Read More</div>
  <div class="abs dots"><span></span><span></span><span class="on"></span><span></span><span></span></div>
</div>

<section class="abs stats">
  <div class="stat" style="left:69px"><b>1800+</b><small>Completed projects</small></div>
  <div class="vline" style="left:320px"></div>
  <div class="stat" style="left:327px"><b>12+</b><small>Years of Experience</small></div>
  <div class="vline" style="left:606px"></div>
  <div class="stat" style="left:607px"><b>1365</b><small>Global Customers</small></div>
  <div class="vline" style="left:889px"></div>
  <div class="stat" style="left:885px"><b>62</b><small>IT Professionals</small></div>
</section>

<section class="about">
  <div class="abs about-photo" role="img" aria-label="Businessman in a suit reading a tablet in a bright office"></div>
  <h2 class="abs h2 about-h">Software Development to<br>help you scale Innovation</h2>
  <div class="abs rule about-rule"></div>
  <p class="abs about-lead">Teams are the essence of every business. They can create wonders if built with perfection.</p>
  <p class="abs about-body">We are a group of entrepreneurs, technocrats, software architects, and delivery heads who have come together to serve startups, product companies, and enterprises with their product development. We are prompt in understanding your product and help design, build, maintain and operate your product. Pellowar quickly set up a team of UX experts, Business Analysts, Developers and QA resources to build the best team to deliver the product.</p>
  <div class="btn" style="left:647px;top:1141px;width:112px;height:35px">Read More</div>
</section>

<h2 class="abs h2 process-h">How can you build software with us?</h2>
<section class="abs process" role="img" aria-label="Dark background of hands working on a laptop">
  <div class="col-alt" style="left:288px;width:315px"></div>
  <div class="col-alt" style="left:899px;width:301px;background:rgba(0,0,0,.15)"></div>
  <div class="row-line"></div>
  <div class="cell" style="left:35px;top:70px">
    <svg width="44" height="50" viewBox="0 0 44 50" fill="none" stroke="#fff" stroke-width="1.6"><circle cx="22" cy="22" r="11"/><path d="M17 33h10v6H17zM19 43h6M22 4v-3M6 8l-2-2M38 8l2-2M2 22h-2M42 22h2"/></svg>
    Brainstorm for a product<br>that will solve a problem</div>
  <div class="cell" style="left:345px;top:70px">
    <svg width="52" height="50" viewBox="0 0 52 50" fill="none" stroke="#fff" stroke-width="1.6"><rect x="2" y="5" width="34" height="43"/><rect x="12" y="1" width="14" height="7"/><path d="M8 17l3 3 5-5M20 18h12M8 28l3 3 5-5M20 29h12M8 39h24"/><rect x="42" y="10" width="6" height="36"/></svg>
    Plan the entire<br>process</div>
  <div class="cell" style="left:646px;top:70px">
    <svg width="62" height="50" viewBox="0 0 62 50" fill="none" stroke="#fff" stroke-width="1.6"><path d="M2 18l12-12 8 6h10l8-6 12 12-8 8-22 16-12-10z"/><path d="M24 20l8 8M20 26l8 8M16 32l6 6"/></svg>
    Incorporate ideas from<br>business partners or<br>stakeholders</div>
  <div class="cell" style="left:941px;top:70px">
    <svg width="54" height="50" viewBox="0 0 54 50" fill="none" stroke="#fff" stroke-width="1.6"><rect x="2" y="4" width="50" height="32"/><path d="M20 36v8h14v-8M14 46h26M8 10h14v20H8zM28 10h18v8H28zM28 22h18v8H28z"/></svg>
    Design the product</div>
  <div class="cell" style="left:35px;top:326px">
    <svg width="52" height="52" viewBox="0 0 52 52" fill="none" stroke="#fff" stroke-width="1.8"><rect x="2" y="2" width="48" height="48" rx="3"/><path d="M2 12h48M19 24l-8 8 8 8M33 24l8 8-8 8M29 22l-6 20"/></svg>
    Outsource the<br>development team</div>
  <div class="cell" style="left:345px;top:326px">
    <svg width="54" height="52" viewBox="0 0 54 52" fill="none" stroke="#fff" stroke-width="1.6"><rect x="2" y="2" width="50" height="36"/><path d="M20 38v8h14v-8M12 48h30"/><circle cx="22" cy="20" r="7"/><path d="M36 28V16M42 28V10M48 28V20"/></svg>
    Develop the product</div>
  <div class="cell" style="left:646px;top:326px">
    <svg width="54" height="52" viewBox="0 0 54 52" fill="none" stroke="#fff" stroke-width="1.6"><rect x="19" y="2" width="16" height="12"/><path d="M27 14v10M8 24h38M8 24v8M46 24v8M27 24v8"/><rect x="2" y="32" width="14" height="12"/><rect x="20" y="32" width="14" height="12"/><rect x="38" y="32" width="14" height="12"/><path d="M2 48h50"/></svg>
    Deploy the product</div>
  <div class="cell" style="left:941px;top:326px">
    <svg width="54" height="54" viewBox="0 0 54 54" fill="none" stroke="#fff" stroke-width="1.8"><circle cx="22" cy="22" r="18"/><circle cx="22" cy="22" r="12"/><path d="M35 35l16 16M16 27v-5M21 27v-9M26 27v-7"/></svg>
    Sell the product to<br>the target market</div>
</section>
<div class="abs process-tick"></div>

<section class="abs why">
</section>
<h2 class="abs h2 why-h">Why Choose Pellowar</h2>
<div class="abs rule why-rule"></div>
<div class="abs features">
  <div>Flexible engagement<br>models</div>
  <div>24x7 support across<br>all timezones</div>
  <div>Competitive pricing &amp;<br>ontime delivery</div>
  <div>Strong technology<br>competency</div>
  <div>Efficient project<br>management</div>
  <div>Progressive<br>roadmap</div>
</div>
<div class="btn" style="left:52px;top:2254px;width:113px;height:35px">Read More</div>
<div class="abs why-photo" role="img" aria-label="Overhead view of a team working at a shared table with laptops"></div>

<section class="build">
  <div class="abs tiles" role="img" aria-label="Laptop screen showing code in a dark room, split into four tiles">
    <div></div><div></div><div></div><div></div>
  </div>
  <h2 class="abs h2 build-h">Build Your Product</h2>
  <div class="abs rule build-rule"></div>
  <div class="abs build-body">
    <p>As startups are racing to build software as a product, they have stumbling blocks on building software from scratch. One of the reasons is stiff competition.</p>
    <p>The competition to get the best resources, robust design, and scalable technology is overwhelming.</p>
    <p>Startup owners must use the CEO mindset while building a software product. Think of the bigger picture. Focus on the outcome and set aside the tiny technical details. Focus on human resources and Process.</p>
  </div>
  <div class="btn" style="left:612px;top:2748px;width:112px;height:35px">Read More</div>
</section>

<section class="abs cta"></section>
<h2 class="abs h2 cta-h">Ready to build your custom software solution?</h2>
<p class="abs cta-sub">Send us your requirement on info@pellowar.com or call +1 555 010 2040</p>
<div class="btn" style="left:497px;top:3030px;width:206px;height:46px;border-radius:10px;font-size:13px">Request a Proposal</div>

<footer class="abs footer">
  <div class="brand"><span class="brand-dot"></span>Pellowar</div>
  <div class="foot-nav">ABOUT US \ &nbsp;PRODUCT \ &nbsp;TEAM &nbsp;\ &nbsp;CASE STUDY \ &nbsp;CONTACT</div>
  <div class="follow">FOLLOW US</div>
  <div class="social" aria-label="Social media links"><span></span><span></span><span></span><span></span></div>
  <div class="copy">Copyright © 2022 All Rights Reserved</div>
</footer>

<form class="abs form">
  <div class="form-h">Get in touch with us<br>Or Send your email at hello@pellowar.com</div>
  <div class="field" style="left:30px;top:108px;width:227px;height:40px">Your Name</div>
  <div class="field" style="left:273px;top:108px;width:227px;height:40px">Your Phone</div>
  <div class="field" style="left:30px;top:165px;width:227px;height:40px">Email</div>
  <div class="field" style="left:273px;top:165px;width:227px;height:40px">Subject</div>
  <div class="field" style="left:30px;top:222px;width:470px;height:92px">Message</div>
  <div class="submit">SUBMIT <svg width="28" height="10" viewBox="0 0 28 10" fill="none" stroke="#fff" stroke-width="1.5"><path d="M0 5h26M21 1l5 4-5 4"/></svg></div>
</form>

</body>
</html>
```